IT Company based on Biology Business Needs a Professional Web Design

We need a professional business website design for a new company called 'Plume KEV'. We develop the machine learning solutions especially focused on deep learning algorithms for biology industry. Our initial product is a vision detection on biological images to help doctors diagnose the symptoms. We would like to see designs that use the color green.

Industry/Entity Type

Business

Number of Pages Required

5+ page

```html
<!DOCTYPE html>
<html lang="en">
<head>
<meta charset="utf-8">
<title>Plume KEV — Deep Learning for Biology</title>
<link rel="stylesheet" href="https://fonts.googleapis.com/css2?family=Open+Sans:wght@400;600;700&family=Raleway:wght@300;400;500&display=swap">
<style>
:root{
  --green:#6cbf1d;
  --green-bright:#7fd11f;
  --green-mid:#4fae16;
  --green-deep:#1c8a3c;
  --green-dark:#137a2d;
  --footer:#137a31;
  --text:#555;
  --text-light:#888;
  --white:#fff;
  --rule:#d8d8d8;
}
*{margin:0;padding:0;box-sizing:border-box}
html,body{width:743px;height:1200px;overflow:hidden;background:var(--white)}
body{position:relative;font-family:"Open Sans",Arial,sans-serif;color:var(--text)}

/* header */
.site-header{position:absolute;left:0;top:0;width:743px;height:69px;border-bottom:1px solid #e2e2e2;background:var(--white)}
.brand{position:absolute;left:106px;top:24px;display:flex;align-items:center;gap:6px;font-family:"Open Sans",sans-serif;font-weight:600;font-size:16px;color:var(--green);letter-spacing:-.3px}
.brand-dot{width:10px;height:10px;border-radius:50%;background:var(--green)}
.main-nav a{position:absolute;top:37px;font-size:9px;color:#222;text-decoration:none;letter-spacing:.1px}
.main-nav a.active{color:var(--green)}

/* hero */
.hero{position:absolute;left:0;top:70px;width:743px;height:288px}
.hero-photo{position:absolute;inset:0;background:radial-gradient(ellipse at 60% 45%,#fff6e8 0%,#f2e8dc 30%,#c9b8cc 60%,#e9e6ee 100%)}
.hero-kicker{position:absolute;left:108px;top:106px;font-weight:700;font-size:17.5px;color:var(--green);letter-spacing:.2px}
.hero-title{position:absolute;left:108px;top:128px;font-weight:700;font-size:26px;color:var(--green-dark);letter-spacing:.3px}
.hero-dots{position:absolute;left:110px;top:178px;display:flex;gap:2px}
.hero-dots span{width:10px;height:10px;border-radius:50%;background:#8a8a8a;border:1px solid #bbb}
.hero-dots span:first-child{background:#aaa}

/* feature band */
.feature{position:absolute;top:358px;height:124px;padding:26px 0 0 0;color:var(--white)}
.feature-what{left:0;width:270px;background:linear-gradient(135deg,var(--green-bright),var(--green-mid))}
.feature-tech{left:270px;width:202px;top:350px;height:132px;padding-top:34px;background:linear-gradient(160deg,#1f9a4a,var(--green-deep))}
.feature-doc{left:472px;width:271px;background:linear-gradient(135deg,var(--green-bright),var(--green-mid))}
.feature h3{font-family:"Open Sans",sans-serif;font-weight:600;font-size:11.5px;letter-spacing:.2px}
.feature .bar{width:18px;height:2px;background:var(--white);margin:5px 0 5px}
.feature p{font-size:6.4px;line-height:12px;width:150px}
.feature-what .inner{margin-left:107px}
.feature-tech .inner{margin-left:25px}
.feature-doc .inner{margin-left:21px}

/* about */
.section-title{font-family:"Raleway",sans-serif;font-weight:400;color:#333}
.about-title{position:absolute;left:104px;top:516px;font-size:20px}
.about-lead{position:absolute;left:104px;top:551px;width:260px;font-size:7.6px;line-height:11px;color:#666}
.about-body{position:absolute;left:104px;top:580px;width:260px;font-size:6.2px;line-height:10.4px;color:#777}
.btn-more{position:absolute;left:104px;top:631px;width:68px;height:20px;background:var(--green-dark);color:var(--white);font-size:7px;line-height:20px;text-align:center;border-radius:2px}
.how-title{position:absolute;left:388px;top:519px;font-size:15.5px}
.how-photo{position:absolute;left:389px;top:548px;width:115px;height:89px;border:1px solid #ccc;background:linear-gradient(135deg,#f0f2f4,#dfe4ea 60%,#c9d3dc)}
.how-lead{position:absolute;left:512px;top:546px;width:130px;font-size:7px;line-height:11px;color:#777}
.how-body{position:absolute;left:512px;top:576px;width:130px;font-size:6px;line-height:11.4px;color:#888}
.rule{position:absolute;left:0;top:689px;width:743px;height:1px;background:var(--rule)}

/* research */
.research-title{position:absolute;left:108px;top:713px;font-size:15.5px;color:var(--green-dark)}
.card{position:absolute;top:745px;width:166px}
.card-photo{height:101px}
.card h4{margin:8px 0 0 3px;font-weight:400;font-size:8.4px;color:var(--green-mid)}
.card p{margin:6px 0 0 3px;width:160px;font-size:6.2px;line-height:11px;color:#777}
.card-1{left:106px}.card-1 .card-photo{background:linear-gradient(135deg,#dde8f2,#9bb4d0 60%,#5d7fa8)}
.card-2{left:290px}.card-2 .card-photo{background:radial-gradient(circle at 50% 55%,#c77b9a 0%,#8c6aa0 35%,#5f7fa8 48%,#eef0f4 52%)}
.card-3{left:474px}.card-3 .card-photo{background:linear-gradient(135deg,#1d4fa8,#3b7fd0 50%,#8fb9e8)}

/* news */
.news{position:absolute;left:0;top:946px;width:743px;height:190px;background:linear-gradient(120deg,#6ccb1e,#4cb81a 50%,#66c421);color:var(--white)}
.news-title{position:absolute;left:105px;top:28px;font-family:"Raleway",sans-serif;font-weight:400;font-size:16px;display:flex;align-items:center;gap:6px}
.news-item{position:absolute;top:64px;width:160px}
.news-date{display:inline-block;background:var(--white);color:#333;font-size:6.8px;line-height:9px;padding:2px 14px 2px 6px;clip-path:polygon(0 0,100% 0,88% 100%,0 100%)}
.news-item h4{font-weight:400;font-size:8.8px;line-height:12px;margin-top:2px}
.news-item p{font-size:6.4px;line-height:10.8px;margin-top:2px}
.news-item .read{display:block;margin-top:6px;font-size:7.6px;font-weight:600}

/* footer */
.site-footer{position:absolute;left:0;top:1136px;width:743px;height:64px;background:var(--footer);color:var(--white)}
.footer-nav{position:absolute;left:106px;top:22px;font-size:6.8px;font-weight:600;letter-spacing:.1px}
.copyright{position:absolute;left:106px;top:39px;font-size:5.6px;color:#cfe9d4}
.social{position:absolute;left:569px;top:17px;display:flex;gap:1px}
.social span{width:18px;height:18px;border:1px solid var(--white);border-radius:50%}
</style>
</head>
<body>

<header class="site-header">
  <div class="brand"><span class="brand-dot"></span>Plume KEV</div>
  <nav class="main-nav">
    <a class="active" style="left:274px">HOME</a>
    <a style="left:328px">ABOUT US</a>
    <a style="left:401px">TECHNOLOGY</a>
    <a style="left:489px">PRODUCTS</a>
    <a style="left:563px">OUR DOCTORS</a>
  </nav>
</header>

<section class="hero">
  <div class="hero-photo" role="img" aria-label="Close-up of a molecular model with glossy spheres and rods on a bright background"></div>
  <div class="hero-kicker">DEEP LEARNING ALGORITHMS</div>
  <div class="hero-title">FOR BIOLOGY INDUSTRY</div>
  <div class="hero-dots"><span></span><span></span><span></span><span></span></div>
</section>

<section class="feature feature-what">
  <div class="inner">
    <h3>WHAT WE DO</h3>
    <div class="bar"></div>
    <p>Morbi diam mauris viverra in gravida eu mattis in ante Morbi eget arcu Morbi porta libero id ullamcorper nonummy nibh ligula pulvinar metus eget consecte</p>
  </div>
</section>
<section class="feature feature-tech">
  <div class="inner">
    <h3>TECHNOLOGY</h3>
    <div class="bar"></div>
    <p>Morbi diam mauris viverra in gravida eu mattis in ante Morbi eget arcu Morbi porta libero id ullamcorper nonummy nibh ligula pulvinar metus eget consecte</p>
  </div>
</section>
<section class="feature feature-doc">
  <div class="inner">
    <h3>OUR DOCTORS</h3>
    <div class="bar"></div>
    <p>Morbi diam mauris viverra in gravida eu mattis in ante Morbi eget arcu Morbi porta libero id ullamcorper nonummy nibh ligula pulvinar metus eget consecte</p>
  </div>
</section>

<section class="about">
  <h2 class="section-title about-title">About Plume KEV</h2>
  <p class="about-lead">Duis sed tellus et tortor vestibulum gravida Praesent elementum elit at tellus Curabitur metus ipsum luctus eu males</p>
  <p class="about-body">Maecenas aliquet velit vel turpis Mauris neque metus malesuada nec ultricies sit amet porttitor mattis enim In massa libero interdum nec interdum vel blandit sed nulla in ullamcorper est eget tempor cursus neque mi consectetuer mi a ultricies massa est sed nisl Class aptent taciti sociosqu ad litora torquent pe</p>
  <div class="btn-more">READ MORE &nbsp;›</div>

  <h2 class="section-title how-title">How it Works</h2>
  <div class="how-photo" role="img" aria-label="Scientist working at a microscope in a laboratory"></div>
  <p class="how-lead">aecenas aliquet velit vel turpis Mauris neque metus malesuada</p>
  <p class="how-body">nec ultricies sit amet porttitor mattis enim In massa libero interdum nec interdum vel blandit sed nulla In ullamcorper est eget tempor cursus neque mi consectetuer mi a ultricies massa est sed nisl</p>
</section>

<div class="rule"></div>

<section class="research">
  <h2 class="section-title research-title">Latest Research</h2>
  <article class="card card-1">
    <div class="card-photo" role="img" aria-label="Gloved hands adjusting a microscope slide"></div>
    <h4>Morbi diam mauris viverra</h4>
    <p>gravida eu mattis in ante Morbi eget arcu Morbi porta libero id ullamcorper nonummy nibh ligula pulvinar metus eget consectetuer</p>
  </article>
  <article class="card card-2">
    <div class="card-photo" role="img" aria-label="Stained cross-section of plant tissue under a microscope"></div>
    <h4>Morbi diam mauris viverra</h4>
    <p>gravida eu mattis in ante Morbi eget arcu Morbi porta libero id ullamcorper nonummy nibh ligula pulvinar metus eget consectetuer</p>
  </article>
  <article class="card card-3">
    <div class="card-photo" role="img" aria-label="Researchers in protective suits handling lab flasks in blue light"></div>
    <h4>Morbi diam mauris viverra</h4>
    <p>gravida eu mattis in ante Morbi eget arcu Morbi porta libero id ullamcorper nonummy nibh ligula pulvinar metus eget consectetuer</p>
  </article>
</section>

<section class="news">
  <h2 class="news-title">Latest News
    <svg width="26" height="22" viewBox="0 0 26 22" aria-hidden="true">
      <g stroke="#fff" stroke-width="1.2" fill="none"><line x1="4" y1="11" x2="13" y2="4"/><line x1="13" y1="4" x2="22" y2="11"/><line x1="4" y1="11" x2="13" y2="18"/><line x1="13" y1="18" x2="22" y2="11"/></g>
      <g fill="#fff"><circle cx="4" cy="11" r="2.6"/><circle cx="13" cy="4" r="2.6"/><circle cx="22" cy="11" r="2.6"/><circle cx="13" cy="18" r="2.6"/></g>
    </svg>
  </h2>
  <article class="news-item" style="left:105px">
    <span class="news-date">15 JAN 2016</span>
    <h4>Mabitur vel mi sit</h4>
    <p>Morbi diam mauris viverra in gravida eu mattis in ante Morbi eget arcu Morbi porta libero id ullamcorper nonummy nibh ligula</p>
    <span class="read">Read More</span>
  </article>
  <article class="news-item" style="left:291px">
    <span class="news-date">19 JAN 2016</span>
    <h4>Proin dui lectus cursus eu mattis</h4>
    <p>Morbi diam mauris viverra in gravida eu mattis in ante Morbi eget arcu Morbi porta libero id ullamcorper nonummy nibh ligula</p>
    <span class="read">Read More</span>
  </article>
  <article class="news-item" style="left:478px">
    <span class="news-date">18 JAN 2016</span>
    <h4>Aliquam erat volutpat Quisque</h4>
    <p>Morbi diam mauris viverra in gravida eu mattis in ante Morbi eget arcu Morbi porta libero id ullamcorper nonummy nibh ligula</p>
    <span class="read">Read More</span>
  </article>
</section>

<footer class="site-footer">
  <div class="footer-nav">HOME &nbsp;|&nbsp; ABOUT US &nbsp;|&nbsp; TECHNOLOGY &nbsp;|&nbsp; PRODUCTS &nbsp;|&nbsp; NEWS &nbsp;|&nbsp; CONTACT</div>
  <div class="copyright">© 2015 Company Name &nbsp;All right reserved &nbsp;Term of Use</div>
  <div class="social" aria-label="Social links"><span></span><span></span><span></span><span></span></div>
</footer>

</body>
</html>
```